We would like a new design for our company Christmas Card. The design must have an orange background and have a festive theme.

The size of the card should be DL (210mm x 99mm).

Message on front cover: Merry Christmas
Message inside: Our warmest wishes for a wonderful Christmas and a very Happy New Year
From the team at under open windows and top-grain

Please see attached example of the card that we used last year.

Industry/Entity Type

It Company

Colors
f78f20

Requirements
Must have
• Orange as the main colour
• A new design
• Font - Helevetica Neue Light (not condensed)

```html
<!DOCTYPE html>
<html lang="en">
<head>
<meta charset="utf-8">
<title>Christmas Card – under open windows and top-grain</title>
<link rel="stylesheet" href="https://fonts.googleapis.com/css2?family=Inter:wght@300;400&display=swap">
<style>
  :root {
    --orange: #f78f20;
    --festive-red: #e8202f;
    --paper: #ffffff;
    --ink: #333333;
    --rule-light: rgba(255, 255, 255, 0.7);
    --backdrop: #ededed;
  }
  * { box-sizing: border-box; margin: 0; padding: 0; }
  html, body {
    width: 1200px;
    height: 1000px;
    overflow: hidden;
    background: var(--backdrop);
    font-family: "Inter", "Helvetica Neue", Helvetica, Arial, sans-serif;
    font-weight: 300;
  }
  .spread {
    position: relative;
    width: 1200px;
    height: 1000px;
  }
  /* DL panel: 210 × 99 mm → 900 × 424 px */
  .card {
    position: absolute;
    left: 150px;
    width: 900px;
    height: 424px;
    overflow: hidden;
  }
  .card--front { top: 56px; background: var(--orange); }
  .card--inside { top: 520px; background: var(--paper); }

  /* Front: a string of festive lights across the panel */
  .light-string {
    position: absolute;
    left: 0;
    top: 0;
    width: 900px;
    height: 200px;
  }
  .front-greeting {
    position: absolute;
    left: 0;
    right: 0;
    top: 250px;
    display: flex;
    justify-content: center;
    align-items: center;
    gap: 18px;
    color: var(--paper);
    font-size: 34px;
    font-weight: 300;
    letter-spacing: 0.18em;
  }
  .front-greeting .dot {
    width: 10px;
    height: 10px;
    border-radius: 50%;
    background: var(--festive-red);
  }
  .front-rule {
    position: absolute;
    left: 330px;
    width: 240px;
    top: 322px;
    height: 1px;
    background: var(--rule-light);
  }

  /* Inside */
  .inside-band {
    position: absolute;
    left: 0;
    top: 0;
    bottom: 0;
    width: 18px;
    background: var(--orange);
  }
  .inside-dots {
    position: absolute;
    left: 0;
    right: 0;
    top: 112px;
    display: flex;
    justify-content: center;
    gap: 10px;
  }
  .inside-dots span {
    width: 8px;
    height: 8px;
    border-radius: 50%;
    background: var(--festive-red);
  }
  .inside-dots span:nth-child(2) { background: var(--orange); }
  .inside-message {
    position: absolute;
    left: 0;
    right: 0;
    top: 156px;
    text-align: center;
    color: var(--ink);
    font-size: 18px;
    line-height: 1.5;
  }
  .inside-signoff {
    position: absolute;
    left: 0;
    right: 0;
    top: 292px;
    text-align: center;
    color: var(--ink);
    font-size: 15px;
  }
</style>
</head>
<body>
<main class="spread">

  <section class="card card--front" aria-label="Card front">
    <svg class="light-string" viewBox="0 0 900 200" aria-hidden="true">
      <path d="M0,40 Q150,150 300,80 T600,80 T900,40" fill="none" stroke="#ffffff" stroke-width="1.5" opacity="0.8"/>
      <g fill="#e8202f">
        <circle cx="75" cy="85" r="7"/>
        <circle cx="225" cy="100" r="7"/>
        <circle cx="375" cy="62" r="7"/>
        <circle cx="525" cy="98" r="7"/>
        <circle cx="675" cy="62" r="7"/>
        <circle cx="825" cy="62" r="7"/>
      </g>
      <g fill="#ffffff">
        <circle cx="150" cy="102" r="5"/>
        <circle cx="300" cy="80" r="5"/>
        <circle cx="450" cy="80" r="5"/>
        <circle cx="600" cy="80" r="5"/>
        <circle cx="750" cy="80" r="5"/>
      </g>
    </svg>
    <p class="front-greeting"><span class="dot"></span>MERRY CHRISTMAS<span class="dot"></span></p>
    <div class="front-rule"></div>
  </section>

  <section class="card card--inside" aria-label="Card inside">
    <div class="inside-band"></div>
    <div class="inside-dots"><span></span><span></span><span></span></div>
    <p class="inside-message">Our warmest wishes<br>for a wonderful Christmas and a very Happy New Year.</p>
    <p class="inside-signoff">From the team at under open windows and top-grain</p>
  </section>

</main>
</body>
</html>
```